The design should look similar to the uploaded example to accommodate the information needed for a business card template. I would like to see the colors orange and charcoal grey incorporated along with the logo.The following should be on the back of the card SPECIALIZING IN NEW AND USED TIRES & WHEELS FOR:- Loaders- Skid Steers- Telehandlers- Boom Lifts- Forklifs and moreELIMINATING DOWNTIMEWheel Exchange Program for New & Used Foam Filled and Solid Rubber TiresSPECIALTY SERVICES- Foam Filling Tires- Largest Tire Press in SE- ONSITE Forklift Tire Press- Boom Truck Services - Rubber Tracks

Target Market(s)

New and Existing Customers

Industry/Entity Type

Business

Contact Information for Business Card

NAMEHEAVY DUTY TIRE, LLC8470 Belvedere RoadWest Palm Beach, FL 33411P: 844-HD-TIRESF: 561-431-6469C:E: W: WWW.GRANITERIMSUPPLY-EXAMPLE.COM

Font styles to use
Sans Serif

Colors
f37122
333333

Requirements
Must have
• The logo and the information indicated for the backside of the card
Nice to have
• Keep the orange and charcoal grey colors

```html
<!DOCTYPE html>
<html lang="en">
<head>
<meta charset="utf-8">
<title>Granite Rim Supply, LLC — Business Card</title>
<link rel="stylesheet" href="https://fonts.googleapis.com/css2?family=Arvo:wght@700&family=Open+Sans:ital,wght@0,400;0,600;0,700;1,400&display=swap">
<style>
  :root {
    --orange: #f37122;
    --charcoal: #333333;
    --navy-charcoal: #37424d;
    --card-dark: #2f3535;
    --paper: #f4f4f4;
    --stage: #8d8d8d;
    --text-grey: #4a4a4a;
    --light: #f1f1f1;
  }
  * { box-sizing: border-box; margin: 0; padding: 0; }
  html, body { width: 1105px; height: 1200px; overflow: hidden; }
  body {
    background: var(--stage);
    font-family: "Open Sans", Arial, sans-serif;
    position: relative;
  }
  .card {
    position: absolute;
    left: 182px;
    width: 747px;
    height: 427px;
    overflow: hidden;
  }
  .card--front { top: 119px; background: var(--paper); }
  .card--back { top: 637px; background: var(--card-dark); }

  /* Front */
  .brand {
    position: absolute;
    left: 319px;
    top: 43px;
    display: flex;
    align-items: center;
    gap: 16px;
  }
  .brand__mark {
    width: 114px; height: 114px;
    border-radius: 50%;
    background: var(--orange);
    flex: none;
  }
  .brand__name {
    font-family: "Arvo", Georgia, serif;
    font-weight: 700;
    font-size: 29px;
    line-height: 38px;
    color: var(--navy-charcoal);
    letter-spacing: 0.5px;
    text-align: center;
  }
  .person {
    position: absolute;
    left: 47px;
    top: 201px;
    right: 41px;
  }
  .person__name {
    font-family: "Arvo", Georgia, serif;
    font-weight: 700;
    font-size: 26px;
    line-height: 32px;
    color: var(--navy-charcoal);
    letter-spacing: 0.5px;
  }
  .person__title-row { display: flex; align-items: flex-end; gap: 6px; }
  .person__title {
    font-size: 18px;
    line-height: 24px;
    color: var(--orange);
    letter-spacing: 0.5px;
  }
  .person__rule { flex: 1; height: 2px; background: var(--orange); margin-bottom: 4px; }

  .contacts {
    position: absolute;
    left: 47px;
    top: 273px;
    list-style: none;
  }
  .contacts li {
    display: flex;
    align-items: center;
    gap: 10px;
    font-size: 18px;
    line-height: 29px;
    color: var(--text-grey);
  }
  .contacts svg { width: 18px; height: 18px; fill: var(--navy-charcoal); flex: none; }

  .address {
    position: absolute;
    right: 41px;
    top: 280px;
    text-align: right;
    font-size: 18px;
    line-height: 28.5px;
    color: var(--text-grey);
    font-style: normal;
  }
  .address__web { letter-spacing: 0.3px; }

  .front-band { position: absolute; left: 0; right: 0; bottom: 0; height: 17px; }

  /* Back */
  .back-mark {
    position: absolute;
    left: -3px;
    top: 40px;
    width: 346px; height: 346px;
    border-radius: 50%;
    background: var(--orange);
    display: flex;
    align-items: center;
    justify-content: center;
  }
  .back-mark__name {
    font-weight: 700;
    font-size: 44px;
    line-height: 52px;
    color: var(--charcoal);
    text-align: center;
  }
  .services {
    position: absolute;
    right: 30px;
    top: 30px;
    text-align: right;
    color: var(--light);
  }
  .services__heading {
    font-weight: 600;
    font-size: 19.5px;
    line-height: 27px;
    color: var(--orange);
  }
  .services__group + .services__group { margin-top: 20px; }
  .services__list { font-style: italic; font-size: 19px; line-height: 27px; }
  .services__body { font-size: 19px; line-height: 27px; }
  .dot { color: var(--orange); font-style: normal; margin: 0 3px; }
</style>
</head>
<body>

<section class="card card--front" aria-label="Business card front">
  <div class="brand">
    <div class="brand__mark" aria-hidden="true"></div>
    <div class="brand__name">GRANITE RIM<br>SUPPLY LLC</div>
  </div>

  <div class="person">
    <div class="person__name">DANIEL REYES</div>
    <div class="person__title-row">
      <span class="person__title">CEO/FOUNDER</span>
      <span class="person__rule"></span>
    </div>
  </div>

  <ul class="contacts">
    <li>
      <svg viewBox="0 0 24 24" aria-hidden="true"><path d="M6.6 10.8a15.1 15.1 0 0 0 6.6 6.6l2.2-2.2c.3-.3.7-.4 1-.2 1.1.4 2.3.6 3.6.6.6 0 1 .4 1 1V20c0 .6-.4 1-1 1A17 17 0 0 1 3 4c0-.6.4-1 1-1h3.5c.6 0 1 .4 1 1 0 1.3.2 2.5.6 3.6.1.3 0 .7-.2 1z"/></svg>
      844-GR-WHEEL
    </li>
    <li>
      <svg viewBox="0 0 24 24" aria-hidden="true"><path d="M7 1h10a2 2 0 0 1 2 2v18a2 2 0 0 1-2 2H7a2 2 0 0 1-2-2V3a2 2 0 0 1 2-2zm0 3v15h10V4zm5 16.2a1 1 0 1 0 0 2 1 1 0 0 0 0-2z"/></svg>
      836 512 7740
    </li>
    <li>
      <svg viewBox="0 0 24 24" aria-hidden="true"><path d="M6 2h12v5H6zM3 8h18a2 2 0 0 1 2 2v7h-4v5H5v-5H1v-7a2 2 0 0 1 2-2zm4 7v5h10v-5z"/></svg>
      561-278-9053
    </li>
    <li>
      <svg viewBox="0 0 24 24" aria-hidden="true"><path d="M2 5h20v14H2zm2 2v.5l8 5 8-5V7zm0 2.8V17h16V9.8l-8 5z"/></svg>
      dreyes@granitewheel.example
    </li>
  </ul>

  <address class="address">
    5126 Marston Lane<br>
    Corvin Springs, GA 30782<br>
    <span class="address__web">www.graniterimsupply-example.com</span>
  </address>

  <svg class="front-band" viewBox="0 0 747 17" preserveAspectRatio="none" aria-hidden="true">
    <polygon points="0,0 490,0 484,17 0,17" fill="var(--navy-charcoal)"/>
    <polygon points="496,0 747,0 747,17 490,17" fill="var(--orange)"/>
  </svg>
</section>

<section class="card card--back" aria-label="Business card back">
  <div class="back-mark">
    <div class="back-mark__name">GRANITE<br>RIM</div>
  </div>

  <div class="services">
    <div class="services__group">
      <h2 class="services__heading">SPECIALIZING IN NEW AND<br>USED TIRES &amp; WHEELS FOR</h2>
      <p class="services__list">Loaders<span class="dot">•</span>Skid Steers<span class="dot">•</span>Telehandlers<span class="dot">•</span><br>Boom Lifts<span class="dot">•</span>Forklifs and more<span class="dot">•</span></p>
    </div>
    <div class="services__group">
      <h2 class="services__heading">ELIMINATING DOWNTIME</h2>
      <p class="services__body">Wheel Exchange Program for New &amp;<br>Used Foam Filled and Solid Rubber Tires</p>
    </div>
    <div class="services__group">
      <h2 class="services__heading">SPECIALTY SERVICES</h2>
      <p class="services__list">Foam Filling Tires<span class="dot">•</span><br>Largest Tire Press in SE<span class="dot">•</span><br>ONSITE Forklift Tire Press<span class="dot">•</span><br>Boom Truck Services<span class="dot">•</span>Rubber Tracks<span class="dot">•</span></p>
    </div>
  </div>
</section>

</body>
</html>
```